New Dental Office Needs an Attractive and user friendly Website Designed

I need a website for a new dental office. The Name is Harrowfield Dentistry. I would like a Modern design with a user friendly interface and usability.
I would like a landing page, a page that lists the services we offer: Cosmetic Dentistry, Implants, Dental Hygiene, Emergency Services, Restorations, Dentures
Target Market(s)
Mid to upper class
Industry/Entity Type
Dentistry
Coding
Number of Pages Required
1 page
Requirements
Must have
- Landing page that has a scheduling option, Procedures, operating hours, and contact us info
Nice to have
- Appealing design, Soft comforting colors. Easy to navigate page, Modern and professional.

```html
<!DOCTYPE html>
<html lang="en">
<head>
<meta charset="utf-8">
<title>Harrowfield Dentistry – Mobile Screens</title>
<link rel="stylesheet" href="https://fonts.googleapis.com/css2?family=Libre+Baskerville:wght@400;700&family=Inter:wght@400;500;600;700&display=swap">
<style>
:root{
  --green:#74bd3c;
  --ink:#1e1e1e;
  --text:#3a3a3a;
  --muted:#8a8a8a;
  --card:#f4f4f4;
  --page:#f6f6f6;
  --white:#ffffff;
  --footer:#252525;
  --quote-mark:#e3f1d5;
  --serif:'Libre Baskerville', Georgia, serif;
  --sans:'Inter', Arial, sans-serif;
}
*{box-sizing:border-box;margin:0;padding:0}
html,body{width:1200px;height:1200px;overflow:hidden;background:var(--page)}
.canvas{position:relative;width:1200px;height:1200px;overflow:hidden}
.stage{position:absolute;left:0;top:0;width:1920px;height:1920px;transform:scale(.625);transform-origin:0 0;font-family:var(--sans);color:var(--text)}
.screen{position:absolute;width:386px;background:var(--white);overflow:hidden;box-shadow:0 10px 60px rgba(0,0,0,.08)}
.screen > *{position:absolute}
.photo{border-radius:12px}
.tone-blue{background:linear-gradient(135deg,#d9e6ee 0%,#b5cad8 45%,#e9eef1 100%)}
.tone-clinic{background:linear-gradient(160deg,#f2f4f5 0%,#dfe5e8 55%,#c8d3d9 100%)}
.tone-warm{background:linear-gradient(135deg,#8aa4b6 0%,#d8c2b4 50%,#eef1f3 100%)}
.tone-soft{background:linear-gradient(150deg,#eef1f2 0%,#d7dfe3 60%,#f5f5f5 100%)}
.tone-deep{background:linear-gradient(135deg,#1e3a6a,#c96f3a)}
.tone-mouth{background:linear-gradient(135deg,#3a1e1a,#e6b9a8)}

.brand{font-family:var(--serif);font-weight:400;font-size:19px;color:var(--ink);display:flex;align-items:center;gap:8px;white-space:nowrap}
.brand-dot{width:10px;height:10px;border-radius:50%;background:var(--ink)}
.menu{width:22px;height:16px;display:flex;flex-direction:column;justify-content:space-between}
.menu span{display:block;height:2.5px;background:var(--ink);border-radius:2px}

.hero-bg{left:0;width:386px;background:linear-gradient(180deg,#ebeef0 0%,#f0f2f4 40%,#eef2f5 70%,#ffffff 100%)}
.hero-title{left:0;width:386px;text-align:center;font-family:var(--serif);color:var(--ink)}
.hero-title.big{font-size:56px;font-weight:700;line-height:60px}
.hero-title.sub{font-size:31px;font-weight:400;line-height:48px}
.hero-text{left:40px;width:306px;text-align:center;font-size:16.5px;line-height:26px;color:var(--ink)}
.btn{display:flex;align-items:center;justify-content:center;gap:10px;border-radius:8px;font-size:15px;white-space:nowrap}
.btn-dark{background:var(--ink);color:var(--white)}
.btn-outline{border:1px solid #9a9a9a;color:var(--ink);background:rgba(255,255,255,.6)}

.eyebrow{left:40px;display:flex;align-items:center;gap:18px;color:var(--green);font-weight:700;font-size:14px;letter-spacing:.2em}
.eyebrow::before{content:"";width:36px;height:1px;background:var(--green)}
.heading{left:40px;width:320px;font-family:var(--serif);font-weight:700;font-size:25px;line-height:34px;color:var(--ink)}
.body{left:40px;width:306px;font-size:13px;line-height:21.5px;color:var(--text);text-align:justify}
.learn{left:40px;font-size:13px;color:var(--muted);display:flex;gap:8px;align-items:center}

.svc{width:148px;text-align:center}
.svc-card{position:absolute;left:0;right:0;bottom:0;background:var(--card);border-radius:10px;padding:46px 12px 0}
.svc-pic{position:absolute;left:34px;top:0;width:80px;height:80px;border-radius:50%;border:3px solid var(--white);z-index:1}
.svc-title{color:var(--green);font-weight:600;font-size:16.5px;line-height:25px}
.svc-desc{font-size:13px;line-height:21.5px;color:var(--text);margin-top:2px}

.why{width:144px;background:var(--card);border-radius:10px;padding:18px}
.why-title{color:var(--green);font-weight:600;font-size:15px;line-height:22.5px}
.why-desc{font-size:13px;line-height:19px;color:var(--text);margin-top:4px}

.contact-row{left:40px;display:flex;gap:12px;align-items:flex-start;font-size:11.5px;color:var(--ink)}
.icon-dot{width:22px;height:22px;border-radius:50%;background:var(--green);display:flex;align-items:center;justify-content:center;flex:none}
.hours{left:72px;font-size:9.5px;color:var(--ink);line-height:18px}
.hours td:first-child{width:62px}

.quote-text{left:148px;width:198px;font-size:9.8px;letter-spacing:-.1px;line-height:18px;text-align:justify;color:var(--ink);z-index:2}
.quote-name{left:148px;color:var(--green);font-weight:600;font-size:14px;z-index:2}
.quote-time{left:148px;color:var(--muted);font-size:10px;z-index:2}
.quote-mark{left:292px;font-family:var(--serif);font-size:110px;line-height:1;color:var(--quote-mark);font-weight:700;z-index:1}
.chev{color:#aaa;font-size:18px}

.footer{left:0;width:386px;background:var(--footer);color:#e8e8e8;text-align:center}
.footer > *{position:absolute;left:0;width:386px}
.footer .brand{color:var(--white);justify-content:center;font-size:17px}
.footer-text{padding:0 40px;font-size:10px;line-height:18px}
.footer-head{font-size:12.5px;font-weight:600;color:var(--white)}
.footer-links{font-size:9.5px;line-height:19.8px}
.socials{display:flex;justify-content:center;gap:6px}
.socials span{width:22px;height:22px;border-radius:5px;background:var(--white)}
.news-input{left:40px!important;width:306px!important;height:31px;border-radius:3px;background:var(--white);color:#999;font-size:9.5px;text-align:left;padding:9px 15px}
.news-btn{left:40px!important;width:306px!important;height:31px;border-radius:3px;background:var(--green);color:var(--white);font-size:10px;line-height:31px}
.footer-rule{left:40px!important;width:306px!important;height:1px;background:#555}
.copy{font-size:9.5px}
</style>
</head>
<body>
<div class="canvas">
<main class="stage">

  <section class="screen" style="left:116px;top:116px;height:1816px">
    <div class="hero-bg" role="img" aria-label="Soft photo of a smiling patient with a dentist" style="top:85px;height:600px"></div>
    <div class="brand" style="left:43px;top:36px"><span class="brand-dot"></span>Harrowfield Dentistry</div>
    <div class="menu" style="left:324px;top:42px"><span></span><span></span><span></span></div>

    <h1 class="hero-title big" style="top:143px">Smile<br>Brighter</h1>
    <p class="hero-title sub" style="top:264px">with Harrowfield<br>Dentistry</p>
    <p class="hero-text" style="top:365px">Personalized and professional dental care in a soothing environment for you and your family.</p>
    <a class="btn btn-dark" style="left:86px;top:470px;width:216px;height:52px">
      <svg width="20" height="20" viewBox="0 0 20 20" fill="none" stroke="#fff" stroke-width="1.4"><rect x="2" y="3.5" width="16" height="14" rx="2.5"/><path d="M2 8h16M6 2v3M14 2v3"/><circle cx="6.5" cy="11.5" r=".6" fill="#fff"/><circle cx="10" cy="11.5" r=".6" fill="#fff"/><circle cx="13.5" cy="11.5" r=".6" fill="#fff"/><circle cx="6.5" cy="14.5" r=".6" fill="#fff"/><circle cx="10" cy="14.5" r=".6" fill="#fff"/></svg>
      Book an Appointment</a>
    <a class="btn btn-outline" style="left:86px;top:532px;width:216px;height:52px">Explore Our Services
      <svg width="12" height="10" viewBox="0 0 12 10" fill="none" stroke="#1e1e1e" stroke-width="1.4"><path d="M0 5h11M7 1l4 4-4 4"/></svg></a>

    <div class="eyebrow" style="top:674px">ABOUT US</div>
    <h2 class="heading" style="top:700px;font-size:24px">Welcome to Harrowfield Dentistry</h2>
    <p class="body" style="top:773px">At Harrowfield Dentistry, we provide top-tier dental care in a warm and relaxing environment. Our team of experienced professionals is dedicated to delivering personalized services using the latest technologies.</p>
    <a class="learn" style="top:910px">Learn more
      <svg width="11" height="9" viewBox="0 0 12 10" fill="none" stroke="#8a8a8a" stroke-width="1.4"><path d="M0 5h11M7 1l4 4-4 4"/></svg></a>
    <div class="photo tone-blue" role="img" aria-label="Dentist examining a smiling patient" style="left:40px;top:956px;width:306px;height:248px"></div>

    <div class="eyebrow" style="top:1265px">OUR SERVICES</div>
    <h2 class="heading" style="top:1284px">Comprehensive Dental Solutions for Every Smile</h2>
    <div class="svc" style="left:40px;top:1406px;height:250px"><div class="svc-pic tone-blue" role="img" aria-label="Patient smiling after cosmetic treatment"></div><div class="svc-card" style="top:48px"><div class="svc-title">Cosmetic<br>Dentistry</div><div class="svc-desc">Enhance your smile with advanced aesthetic treatments.</div></div></div>
    <div class="svc" style="left:198px;top:1406px;height:250px"><div class="svc-pic tone-warm" role="img" aria-label="Dental implant model"></div><div class="svc-card" style="top:48px"><div class="svc-title">Dental<br>Implants</div><div class="svc-desc">Natural-looking replacements for missing teeth.</div></div></div>
    <div class="svc" style="left:40px;top:1677px;height:250px"><div class="svc-pic tone-soft" role="img" aria-label="Patient at a hygiene visit"></div><div class="svc-card" style="top:48px"><div class="svc-title">Dental Hygiene</div><div class="svc-desc">Preventative care for long-lasting oral health.</div></div></div>
    <div class="svc" style="left:198px;top:1677px;height:250px"><div class="svc-pic tone-deep" role="img" aria-label="Urgent dental treatment under lamp"></div><div class="svc-card" style="top:48px"><div class="svc-title">Emergency<br>Services</div><div class="svc-desc">Fast and effective care when you need it most.</div></div></div>
  </section>

  <section class="screen" style="left:554px;top:0;height:1932px">
    <div class="photo tone-blue" role="img" aria-label="Dentist examining a smiling patient" style="left:40px;top:-104px;width:306px;height:249px"></div>
    <div class="eyebrow" style="top:206px">OUR SERVICES</div>
    <h2 class="heading" style="top:226px">Comprehensive Dental Solutions for Every Smile</h2>
    <div class="svc" style="left:40px;top:348px;height:250px"><div class="svc-pic tone-blue" role="img" aria-label="Patient smiling after cosmetic treatment"></div><div class="svc-card" style="top:48px"><div class="svc-title">Cosmetic<br>Dentistry</div><div class="svc-desc">Enhance your smile with advanced aesthetic treatments.</div></div></div>
    <div class="svc" style="left:198px;top:348px;height:250px"><div class="svc-pic tone-warm" role="img" aria-label="Dental implant model"></div><div class="svc-card" style="top:48px"><div class="svc-title">Dental<br>Implants</div><div class="svc-desc">Natural-looking replacements for missing teeth.</div></div></div>
    <div class="svc" style="left:40px;top:618px;height:230px"><div class="svc-pic tone-soft" role="img" aria-label="Patient at a hygiene visit"></div><div class="svc-card" style="top:48px"><div class="svc-title">Dental Hygiene</div><div class="svc-desc">Preventative care for long-lasting oral health.</div></div></div>
    <div class="svc" style="left:198px;top:618px;height:230px"><div class="svc-pic tone-deep" role="img" aria-label="Urgent dental treatment under lamp"></div><div class="svc-card" style="top:48px"><div class="svc-title">Emergency<br>Services</div><div class="svc-desc">Fast and effective care when you need it most.</div></div></div>
    <div class="svc" style="left:40px;top:868px;height:204px"><div class="svc-pic tone-mouth" role="img" aria-label="Close view of a tooth restoration"></div><div class="svc-card" style="top:48px"><div class="svc-title">Restorations</div><div class="svc-desc">Repair and restore damaged teeth to full function.</div></div></div>
    <div class="svc" style="left:198px;top:868px;height:204px"><div class="svc-pic tone-warm" role="img" aria-label="Hands holding a denture"></div><div class="svc-card" style="top:48px"><div class="svc-title">Dentures</div><div class="svc-desc">Comfortable and natural-looking tooth replacements.</div></div></div>

    <div class="photo tone-clinic" role="img" aria-label="Dentist standing in a bright treatment room" style="left:40px;top:1135px;width:306px;height:248px"></div>
    <div class="eyebrow" style="top:1410px">APPOINTMENT</div>
    <h2 class="heading" style="top:1432px">Ready to Smile Confidently?</h2>
    <p class="body" style="top:1508px">Scheduling an appointment with Harrowfield Dentistry is simple and stress-free. Whether you’re a new or returning patient, we’re here to make your dental care as convenient as possible.</p>
    <a class="btn btn-dark" style="left:40px;top:1613px;width:225px;height:49px;font-size:13px">Book Your Appointment Now
      <svg width="11" height="9" viewBox="0 0 12 10" fill="none" stroke="#fff" stroke-width="1.4"><path d="M0 5h11M7 1l4 4-4 4"/></svg></a>
    <div class="eyebrow" style="top:1725px">WHY CHOOSE US</div>
    <h2 class="heading" style="top:1747px">Why Choose Harrowfield Dentistry?</h2>
    <div class="why" style="left:40px;top:1832px;height:139px"><div class="why-title">Trusted Professionals</div><div class="why-desc">Skilled dentists with years of experience.</div></div>
    <div class="why" style="left:202px;top:1832px;height:139px"><div class="why-title">Relaxing Environment</div><div class="why-desc">Designed for your comfort and peace of mind.</div></div>
  </section>

  <section class="screen" style="left:992px;top:0;height:1932px">
    <div class="svc" style="left:40px;top:-97px;height:225px"><div class="svc-pic tone-soft"></div><div class="svc-card" style="top:48px"><div class="svc-title">Dental Hygiene</div><div class="svc-desc">Preventative care for long-lasting oral health.</div></div></div>
    <div class="svc" style="left:198px;top:-115px;height:243px"><div class="svc-pic"></div><div class="svc-card" style="top:48px"><div class="svc-title">Emergency<br>Services</div><div class="svc-desc">Fast and effective care when you need it most.</div></div></div>
    <div class="svc" style="left:40px;top:150px;height:203px"><div class="svc-pic tone-mouth" role="img" aria-label="Close view of a tooth restoration"></div><div class="svc-card" style="top:48px"><div class="svc-title">Restorations</div><div class="svc-desc">Repair and restore damaged teeth to full function.</div></div></div>
    <div class="svc" style="left:198px;top:150px;height:203px"><div class="svc-pic tone-warm" role="img" aria-label="Hands holding a denture"></div><div class="svc-card" style="top:48px"><div class="svc-title">Dentures</div><div class="svc-desc">Comfortable and natural-looking tooth replacements.</div></div></div>

    <div class="photo tone-clinic" role="img" aria-label="Dentist standing in a bright treatment room" style="left:40px;top:417px;width:306px;height:248px"></div>
    <div class="eyebrow" style="top:692px">APPOINTMENT</div>
    <h2 class="heading" style="top:714px">Ready to Smile Confidently?</h2>
    <p class="body" style="top:790px">Scheduling an appointment with Harrowfield Dentistry is simple and stress-free. Whether you’re a new or returning patient, we’re here to make your dental care as convenient as possible.</p>
    <a class="btn btn-dark" style="left:40px;top:895px;width:225px;height:48px;font-size:13px">Book Your Appointment Now
      <svg width="11" height="9" viewBox="0 0 12 10" fill="none" stroke="#fff" stroke-width="1.4"><path d="M0 5h11M7 1l4 4-4 4"/></svg></a>
    <div class="eyebrow" style="top:1007px">WHY CHOOSE US</div>
    <h2 class="heading" style="top:1029px">Why Choose Harrowfield Dentistry?</h2>
    <div class="why" style="left:40px;top:1114px;height:139px"><div class="why-title">Trusted Professionals</div><div class="why-desc">Skilled dentists with years of experience.</div></div>
    <div class="why" style="left:202px;top:1114px;height:139px"><div class="why-title">Relaxing Environment</div><div class="why-desc">Designed for your comfort and peace of mind.</div></div>
    <div class="why" style="left:40px;top:1272px;height:159px"><div class="why-title">Advanced Technology</div><div class="why-desc">Digital imaging, modern tools, and precision techniques.</div></div>
    <div class="why" style="left:202px;top:1272px;height:159px"><div class="why-title">Flexible Scheduling</div><div class="why-desc">Extended hours and same-day appointments available.</div></div>
    <div class="photo tone-blue" role="img" aria-label="Patient smiling during a dental check-up" style="left:40px;top:1458px;width:306px;height:248px"></div>
    <div class="photo tone-soft" role="img" aria-label="Dentist in a white coat in the clinic" style="left:40px;top:1770px;width:306px;height:248px"></div>
  </section>

  <section class="screen" style="left:1430px;top:0;height:1816px">
    <div class="photo tone-blue" role="img" aria-label="Patient smiling during a dental check-up" style="left:40px;top:-46px;width:306px;height:248px"></div>
    <div class="photo tone-soft" role="img" aria-label="Dentist in a white coat in the clinic" style="left:40px;top:265px;width:306px;height:248px"></div>

    <div class="eyebrow" style="top:540px">CONTACT US</div>
    <h2 class="heading" style="top:566px">We're Here for You</h2>
    <div class="contact-row" style="top:610px"><span class="icon-dot"><svg width="11" height="12" viewBox="0 0 12 14" fill="none" stroke="#fff" stroke-width="1.4"><path d="M6 13s5-4.5 5-8a5 5 0 0 0-10 0c0 3.5 5 8 5 8z"/><circle cx="6" cy="5" r="1.6"/></svg></span><span style="padding-top:4px">123 Harrowfield Avenue, City, State, ZIP</span></div>
    <div class="contact-row" style="top:641px"><span class="icon-dot"><svg width="11" height="11" viewBox="0 0 12 12" fill="none" stroke="#fff" stroke-width="1.3"><path d="M2 1h2.5l1 3-1.5 1a7 7 0 0 0 3 3l1-1.5 3 1V10a1 1 0 0 1-1 1A9.5 9.5 0 0 1 1 2a1 1 0 0 1 1-1z"/></svg></span><span style="padding-top:4px">+(555) 987-2410</span></div>
    <div class="contact-row" style="top:672px"><span class="icon-dot"><svg width="11" height="9" viewBox="0 0 12 10" fill="none" stroke="#fff" stroke-width="1.3"><rect x=".7" y=".7" width="10.6" height="8.6" rx="1"/><path d="M1 1.5l5 4 5-4"/></svg></span><span style="padding-top:4px">hello@harrowfielddentistry.com</span></div>
    <div class="contact-row" style="top:704px"><span class="icon-dot"><svg width="11" height="11" viewBox="0 0 12 12" fill="none" stroke="#fff" stroke-width="1.3"><circle cx="6" cy="6" r="5"/><path d="M6 3v3l2 1.5"/></svg></span><span style="padding-top:4px">Open Hours</span></div>
    <table class="hours" style="top:725px">
      <tr><td>Mon – Fri</td><td>9:00 AM – 6:00 PM</td></tr>
      <tr><td>Sat</td><td>9:00 AM – 1:00 PM</td></tr>
      <tr><td>Sun</td><td>Closed</td></tr>
    </table>

    <div class="eyebrow" style="top:828px">TESTIMONIALS</div>
    <h2 class="heading" style="top:851px">What Our Patients Are Saying?</h2>
    <div class="photo tone-warm" role="img" aria-label="Portrait of a patient" style="left:40px;top:932px;width:90px;height:198px;border-radius:8px"></div>
    <p class="quote-text" style="top:933px">My experience at Harrowfield Dentistry was outstanding. The staff was warm and welcoming, and the clinic had a clean, calming atmosphere. Dr. Lindqvist was professional, explained everything clearly, and made me feel completely at ease. I finally found a dental office that truly cares about its patients.</p>
    <div class="quote-mark" style="top:1080px">”</div>
    <div class="quote-name" style="top:1094px">Maren T.</div>
    <div class="quote-time" style="top:1115px">10 hours ago</div>
    <div class="chev" style="left:13px;top:1018px">‹</div>
    <div class="chev" style="left:361px;top:1018px">›</div>

    <footer class="footer" style="top:1193px;height:623px">
      <div class="brand" style="top:36px">Harrowfield Dentistry</div>
      <p class="footer-text" style="top:72px">Exceptional dental care in a calming, modern environment. We’re dedicated to helping you smile with confidence through personalized, professional service.</p>
      <div class="footer-head" style="top:142px">Quick Links</div>
      <div class="footer-links" style="top:164px">Home<br>Our Services<br>About Us<br>Testimonials<br>Contact<br>Schedule Appointment</div>
      <div class="footer-head" style="top:299px">Company</div>
      <div class="footer-links" style="top:321px">Support<br>Privacy policy<br>Terms of service</div>
      <div class="footer-head" style="top:396px">Stay Connected</div>
      <div class="socials" style="top:421px"><span></span><span></span><span></span></div>
      <div class="footer-head" style="top:463px">Newsletter</div>
      <div class="news-input" style="top:491px">Write your email</div>
      <div class="news-btn" style="top:528px">Subscribe</div>
      <div class="footer-rule" style="top:586px"></div>
      <div class="copy" style="top:599px">© 2025 Harrowfield Dentistry. All Rights Reserved.</div>
    </footer>
  </section>

</main>
</div>
</body>
</html>
```